Business cards for 3 Realtors at one brokerage

We will need a business card template that can be projected on 3 business cards. Harborline Realty & Investment Corp. has 3 realtors on staff Dane, Owen, and Miles. We all want a business card that shows our new logo and information. I will attach many versions of our Logo as well as head shots for each realtor (Owen- Long hair, youngest. Miles- Suit jacket, parted hair cut. Dane- Angled Pose, Shirt and Tie.) I have attached our information below.

Dane Foskett
801-555-0147
dane@harborlinehomesite.com
Principal Broker

Miles Tandrow
801-555-0162
miles@harborlinehomesite.com
Real Estate Agent

Owen Tandrow
801-555-0138
owen@harborlinehomesite.com
Real Estate Agent

Harborline Realty & Investment Corp.
HarborlineHomesite.com
5286 N 7200 Suite 208-617, Cedar Hollow, UT 84990

Please feel free to reach out with any questions, comments, or concerns.

```html
<!DOCTYPE html>
<html lang="en">
<head>
<meta charset="utf-8">
<title>Harborline Realty – Business Card</title>
<link rel="stylesheet" href="https://fonts.googleapis.com/css2?family=Poppins:wght@400;500;600&display=swap">
<style>
  :root {
    --backdrop: #dee4ea;
    --paper: #ffffff;
    --brand-blue: #36a8f8;
    --brand-blue-faint: #56b7fa;
    --ink-gray: #666666;
    --band-gray: #858585;
    --photo-tone: #d9dbd8;
  }
  * { box-sizing: border-box; margin: 0; padding: 0; }
  html, body {
    width: 1200px; height: 806px; overflow: hidden;
    background: var(--backdrop);
    font-family: "Poppins", sans-serif;
  }
  .card {
    position: absolute; top: 301px;
    width: 330px; height: 204px; overflow: hidden;
    box-shadow: 0 1px 1.5px rgba(0,0,0,.35);
  }
  .card-front { left: 255px; background: var(--paper); }
  .card-back { left: 615px; background: var(--brand-blue); color: var(--paper); }

  /* front */
  .brand-mark {
    position: absolute; left: 61px; top: 17px;
    width: 42px; height: 42px; border-radius: 50%;
    border: 2.5px solid var(--brand-blue);
  }
  .brand-name {
    position: absolute; left: 0; width: 164px; top: 60px;
    text-align: center; color: var(--ink-gray); font-weight: 500;
    font-size: 12px; line-height: 14px; white-space: nowrap;
  }
  .brand-name small {
    display: block; font-size: 5px; line-height: 7px; letter-spacing: 1.3px;
  }
  .name-band {
    position: absolute; left: 0; top: 95px; width: 176px; height: 42px;
    background: var(--brand-blue); color: var(--paper);
    padding: 9px 0 0 27px;
  }
  .agent-name { font-size: 11.5px; font-weight: 600; line-height: 14px; }
  .agent-title { font-size: 9.5px; font-weight: 500; line-height: 12px; }
  .accent-band {
    position: absolute; left: 314px; top: 95px; width: 16px; height: 42px;
    background: var(--band-gray);
  }
  .portrait-frame { position: absolute; left: 174px; top: 44px; }
  .contact-list {
    position: absolute; left: 27px; top: 146px; list-style: none;
    color: var(--ink-gray); font-size: 9px; line-height: 12.6px; white-space: nowrap;
  }
  .contact-list li { display: flex; align-items: center; gap: 3px; }
  .contact-list svg { flex: none; }
  .contact-list .highlight { color: var(--brand-blue); }

  /* back */
  .back-decor { position: absolute; left: 0; top: 0; }
  .back-mark {
    position: absolute; left: 135px; top: 35px;
    width: 60px; height: 60px; border-radius: 50%;
    border: 3px solid var(--paper);
  }
  .back-brand {
    position: absolute; left: 0; width: 330px; top: 100px;
    text-align: center; font-weight: 500; font-size: 17px; line-height: 20px;
  }
  .back-brand small {
    display: block; font-size: 7px; line-height: 10px; letter-spacing: 2px;
  }
  .location-divider { position: absolute; left: 120px; top: 139px; }
  .back-address {
    position: absolute; left: 0; width: 330px; top: 153px;
    text-align: center; font-size: 9.8px; line-height: 12.6px; white-space: nowrap;
  }
  .back-address .street { font-weight: 500; }
</style>
</head>
<body>
  <section class="card card-front">
    <div class="brand-mark"></div>
    <p class="brand-name">HARBORLINE REALTY<small>&amp; INVESTMENT CORP.</small></p>

    <div class="name-band">
      <p class="agent-name">OWEN TANDROW</p>
      <p class="agent-title">Real Estate Agent</p>
    </div>
    <div class="accent-band"></div>

    <svg class="portrait-frame" width="142" height="142" viewBox="0 0 142 142">
      <circle cx="71" cy="71" r="70" fill="var(--paper)"/>
      <circle cx="71" cy="71" r="64" fill="none" stroke="var(--brand-blue)" stroke-width="5.5"
              stroke-dasharray="360 42" transform="rotate(-118 71 71)"/>
      <circle cx="71" cy="71" r="54" fill="none" stroke="var(--brand-blue)" stroke-width="2.5"/>
      <circle cx="71" cy="71" r="52" fill="var(--photo-tone)" role="img"
              aria-label="Headshot of agent Owen Tandrow"/>
    </svg>

    <ul class="contact-list">
      <li>
        <svg width="11" height="11" viewBox="0 0 12 12"><circle cx="6" cy="6" r="6" fill="var(--brand-blue)"/><path d="M4 3.2l1.1 1.5-.6.7c.4.9 1.1 1.6 2 2l.7-.6L8.8 8c-.3.6-.8.9-1.3.8C5.6 8.4 3.6 6.4 3.2 4.5c-.1-.5.2-1 .8-1.3z" fill="var(--paper)"/></svg>
        801-555-0138
      </li>
      <li>
        <svg width="11" height="11" viewBox="0 0 12 12"><circle cx="6" cy="6" r="6" fill="var(--brand-blue)"/><rect x="3" y="4" width="6" height="4.2" fill="var(--paper)"/><path d="M3 4l3 2.3L9 4" fill="none" stroke="var(--brand-blue)" stroke-width=".7"/></svg>
        owen@harborlinehomesite.com
      </li>
      <li>
        <svg width="11" height="11" viewBox="0 0 12 12"><circle cx="6" cy="6" r="6" fill="var(--brand-blue)"/><g fill="none" stroke="var(--paper)" stroke-width=".7"><circle cx="6" cy="6" r="3.2"/><ellipse cx="6" cy="6" rx="1.4" ry="3.2"/><path d="M2.8 6h6.4"/></g></svg>
        <span>www.<span class="highlight">HarborlineHomesite</span>.com</span>
      </li>
    </ul>
  </section>

  <section class="card card-back">
    <svg class="back-decor" width="330" height="204" viewBox="0 0 330 204">
      <circle cx="280" cy="102" r="96" fill="none" stroke="var(--brand-blue-faint)" stroke-width="9"/>
    </svg>
    <div class="back-mark"></div>
    <p class="back-brand">HARBORLINE REALTY<small>&amp; INVESTMENT CORP.</small></p>

    <svg class="location-divider" width="90" height="16" viewBox="0 0 90 16">
      <path d="M0 8h28M62 8h28" stroke="var(--paper)" stroke-width=".8"/>
      <path d="M45 15c-3-3.6-6.5-6.6-6.5-9a6.5 6.5 0 0 1 13 0c0 2.4-3.5 5.4-6.5 9z" fill="var(--paper)"/>
      <circle cx="45" cy="6" r="2" fill="var(--brand-blue)"/>
    </svg>

    <div class="back-address">
      <p class="street">5286 N 7200 Suite 208-617, Cedar Hollow, UT 84990</p>
      <p>www.HarborlineHomesite.com</p>
    </div>
  </section>
</body>
</html>
```